Hurricane Damage Public Adjuster Billboard

I have created several projects with you and have several great designs. I need to format them into a Billboard for upcoming Hurricane Season. Need done in a month. Im also in process of getting an eye catching and easy to remember 800# Vanity phone number like Call 800-Stormsafe or 800- Need Fix? My included past Craft Huddle projects will give you an idea of what colors, schemes, and designs I gravitate towards. 3 past Design projects were 1) 2 Logos where I picked the 1st place and the 2nd place and 2) Index Card where I picked the winner as the Index Card and the 2nd place as a Post Card. Point is, I will pick and pay for 2 winners if they're good. This should help to sweeten the pot. Also, please look at my website for ideas that I like:

www.TheClaimKeeperGroup.com
I want people to feel that I am the best and highest. Level.

I've been getting a lot of quick half effort designs basically cut & pasting my previous projects. Please don't rush and take your time to be creative. A an example, my Biggest Competitor is Vesta Public Adjusting. Their colors are Black and Gold while mine are Blue, White, and Black with a highlight of Orange if possible. I JUST imported a picture of their BillBoard. I need mine better and BLOW AWAY THEIRS. Terms like "Don't be Victimized Twice ?, Don't let the Hurricane Ruin your Life?". "Get Fairly Paid & Move On" "Our Clients Claims are VIP?
Updates

I'm getting a lot of quick half effort ones. I'd rather you take your time and really put some thoughts and effort into it. My Biggest Competitor is Vesta Public Adjusting. They have black & gold colors, while I have Blue, Black, and white.

It needs to blow theirs away. I have imported their Billboard for comparative purposes.

Guy's,
I'll make it easier for you in what I'm looking for. Please look at the Vesta Billboard picture attached.

1) Put my "Blue Shield" to the left, replacing their logo
2) change color patterns from their (Black, Gold, White) to my color schemes of (Black, Blue, White)
3) I want to see my name where their is:

THE
Claim Keeper's Group
EXPERT & LOCAL Public Adjusters
"FOR THE POLICYHOLDER!!"

4) to the right, add the A+Rated logo and QRS+ Accredited logo, 5 Star Zorbix Rated logo, 5 Start PORCHLINE Highly Rated logo, etc..

5) the right side is where you can be creative as I will not have a picture of me there.

"20+ Years of Experience, Recovering Millions for our VIP Clients"

"Your Best, Locally-Based Private Adjuster & Advocate'
"FOR THE POLICYHOLDER!!"

"Don't be victimized Twice!!"

"Don't let the Hurricane Ruin Your Life!!"

This should really help. Also, refer to my website, maybe a couple testimonial fillers?

Thanks all,

marcus@TheClaimKeeperGroup.com

Just imported a few awards that would look great to the right side with all the other 5 Star Ratings and accolades.
This right section could be titled like zmy Website:

5 Star Reviews, Ratings & Awards:
4-5 Logos underneath?

Target Market(s)

Coastal place where a Hurricane 🌀 🌀 Hits

Industry/Entity Type

Hurricane Public Insurance Adjuster

Font styles to use
Sans Serif
Other font styles liked:
• Zurich fonts

Colors
0054AA
0677BA
7BADD7
CADEEF
E8F1F8
EE7325
F08F49
F5BC92
FAE3D3
FDF4ED

Requirements
Must have
• Use my past project logos, colors, and schemes to create eye grabbing BillBoard
Nice to have
Should not have
• Not be too busy, must be Easy to Read, Eye Catchy

```html
<!DOCTYPE html>
<html lang="en">
<head>
<meta charset="utf-8">
<title>Claim Keeper's Group – Hurricane Billboard</title>
<link href="https://fonts.googleapis.com/css2?family=Bebas+Neue&family=Poppins:wght@500;600;700;800&display=swap" rel="stylesheet">
<style>
  :root{
    --blue-deep:#0054AA;
    --blue:#0677BA;
    --blue-bright:#0A9BE0;
    --blue-light:#7BADD7;
    --orange:#EE7325;
    --orange-soft:#F08F49;
    --navy:#06121f;
    --ink:#141414;
    --panel:#ECEEF0;
    --white:#FFFFFF;
    --red:#E0262B;
    --teal:#0D5C72;
    --green:#6CC04A;
  }
  *{box-sizing:border-box;margin:0;padding:0}
  html,body{width:960px;height:1200px;overflow:hidden;background:var(--white)}
  .canvas{position:relative;width:960px;height:1200px;background:var(--white)}
  .billboard{
    position:absolute;left:20px;top:466px;width:920px;height:268px;
    background:var(--white);box-shadow:0 6px 18px rgba(0,0,0,.25);
    font-family:'Poppins',sans-serif;overflow:hidden;
  }
  .billboard-shapes{position:absolute;inset:0}
  .t{position:absolute;white-space:nowrap;line-height:1}
  .brand-name{left:14px;top:52px;width:168px;white-space:normal;text-align:center;
    color:var(--white);font-weight:700;font-size:20px;line-height:1.2}
  .kicker{left:197px;top:24px;color:var(--white);font-weight:600;font-size:31px}
  .headline{left:197px;top:54px;color:var(--blue-bright);font-family:'Bebas Neue',sans-serif;font-weight:400;font-size:62px}
  .tagline{left:197px;top:108px;color:var(--orange);font-weight:500;font-size:29px}
  .band-left{left:158px;top:157px;color:var(--white);font-weight:600;font-size:15.5px}
  .band-right{left:482px;top:155px;color:var(--white);font-weight:700;font-size:20px}
  .years-num{left:38px;top:196px;color:var(--blue);font-weight:700;font-size:56px;letter-spacing:-2px}
  .years-label{left:150px;top:203px;color:var(--ink);font-weight:700;font-size:16.5px;line-height:1.2}
  .years-note{left:40px;top:246px;color:var(--ink);font-weight:700;font-size:9.3px}
  .call{left:382px;top:207px;color:var(--ink);font-weight:800;font-size:41px;letter-spacing:-.5px}
  .rating{left:806px;top:24px;width:76px;text-align:center;color:var(--red);font-weight:700;font-size:16px}
  .rating-note{left:796px;top:43px;width:96px;text-align:center;color:#333;font-weight:500;font-size:5.6px;line-height:1.15;white-space:normal}
  .reviews-name{left:800px;top:101px;width:88px;text-align:center;color:var(--blue);font-weight:600;font-size:21px}
  .reviews-stars{left:800px;top:126px;width:88px;text-align:center;color:#555;font-weight:500;font-size:8px}
  .reviews-stars span{color:var(--orange)}
  .porch{left:796px;top:144px;width:96px;text-align:center;color:var(--green);font-weight:700;font-size:13px}
</style>
</head>
<body>
<main class="canvas">
  <section class="billboard" aria-label="Claim Keeper's Group hurricane billboard">
    <svg class="billboard-shapes" width="920" height="268" viewBox="0 0 920 268">
      <defs>
        <linearGradient id="storm" x1="0" y1="0" x2="1" y2="1">
          <stop offset="0" stop-color="#050a12"/>
          <stop offset=".55" stop-color="#0b2236"/>
          <stop offset="1" stop-color="#1b4d74"/>
        </linearGradient>
        <linearGradient id="brandBlue" x1="0" y1="0" x2="0" y2="1">
          <stop offset="0" stop-color="#16A3E3"/>
          <stop offset="1" stop-color="#0677BA"/>
        </linearGradient>
      </defs>
      <rect class="storm-sky" x="0" y="0" width="920" height="188" fill="url(#storm)" role="img" aria-label="Dark stormy sky with lightning strikes"/>
      <polygon class="brand-corner" points="0,0 190,0 190,188 0,188" fill="url(#brandBlue)"/>
      <polygon class="ratings-edge" points="796,0 920,0 920,188 806,188 740,100" fill="var(--blue-bright)"/>
      <polygon class="ratings-panel" points="808,0 920,0 920,188 818,188 752,100" fill="var(--panel)"/>
      <polygon class="band-blue" points="0,145 471,145 444,188 0,188" fill="var(--blue-bright)"/>
      <polygon class="band-orange" points="471,145 782,145 812,188 444,188" fill="var(--orange)"/>
      <rect class="award-badge" x="265" y="201" width="43" height="52" rx="3" fill="#3a4a6a" role="img" aria-label="2022 award badge"/>
      <rect class="rating-badge" x="808" y="68" width="72" height="26" rx="3" fill="var(--teal)" role="img" aria-label="Accredited business badge"/>
      <g class="phone-icon" transform="translate(340,210)">
        <circle cx="18" cy="18" r="17" fill="var(--orange)"/>
        <path d="M11 10 c2-1 3 0 4 2 l1 3 c0 1-1 2-2 2 c1 3 3 5 6 6 c0-1 1-2 2-2 l3 1 c2 1 3 2 2 4 c-1 2-3 3-5 2 c-6-2-10-6-12-12 c-1-2 0-5 1-6z" fill="var(--white)"/>
      </g>
    </svg>

    <p class="t brand-name">Claim Keeper's Group</p>

    <p class="t kicker">DON'T LET THE</p>
    <h1 class="t headline">HURRICANE RUIN YOUR LIFE?</h1>
    <p class="t tagline">THE Claim Keeper's Group</p>

    <p class="t band-left">EXPERT &amp; LOCAL Public Adjusters</p>
    <p class="t band-right">FOR THE POLICYHOLDER!</p>

    <p class="t years-num">20+</p>
    <p class="t years-label">YEARS OF<br>EXPERIENCE</p>
    <p class="t years-note">RECOVERING MILLIONS FOR OUR VIP CLIENTS</p>

    <p class="t call">CALL 800-STORMSAFE</p>

    <p class="t rating">A+ Rating</p>
    <p class="t rating-note">Highest Rating For Public Insurance Adjusters (Source: RatingPanel)</p>
    <p class="t reviews-name">Zorbix</p>
    <p class="t reviews-stars">Reviews <span>★★★★★</span></p>
    <p class="t porch">PORCHLINE</p>
  </section>
</main>
</body>
</html>
```